Business Card Design Project

We need a business card for a new technology services company. We develop software and implement software packages for our business customers and although we will begin with just one or two service offerings, our service offerings will expand over time. Our name comes from the an author, KL Barrow, and his "idea" was that opportunity should be based on ability and achievement, not on social status.

We would like to see a design that is standard in its size and shape, but stands apart in its dramatic color contrasts. The card should not use too many colors - the colors used in the background should highlight the brilliant blues of the logo (see attachment) to dramatic effect. The background should not be white.

If necessary, you can change the color of the words "KL Barrow", but not the word "Idea".

Card size should be U.S. standard 2 inches by 3.5 inches and provide for 1/8 inch bleed area on each side.

We need a design for both sides of the business card, one side communicating the company logo and contact information, the other side being purely graphical, incorporating the logo but no other information.

Contact Information Required:
Kate Brook
KateBrook@klbarrowvista.com
614-387-2259

Target Market(s)

Business executives

Industry/Entity Type

Software

Requirements
Must have
• It must have the full company logo on one side, and at least the graphic element of the logo on the other. Either that or the full logo on both.
Nice to have
• It would be nice to have a design that could work without needing two different textures. For example, it would be nice if the entire card could be shiny, not just parts of the card.

It would also be nice if texture is something we could add later.
Should not have
• The card should not use the color green.

```html
<!DOCTYPE html>
<html lang="en">
<head>
<meta charset="utf-8">
<title>Halvern Works – Business Card</title>
<link rel="stylesheet" href="https://fonts.googleapis.com/css2?family=Cinzel:wght@600&family=Roboto:wght@400&display=swap">
<style>
  :root {
    --canvas-bg: #e9e7ec;
    --card-dark: #2a2433;
    --card-mid: #3e3549;
    --card-light: #5a4e66;
    --brand-blue: #1aa3e0;
    --brand-blue-deep: #0f86c4;
    --wordmark-grey: #b4b1b8;
    --contact-white: #f2f2f4;
    --swoosh-silver: #c9c7cf;
    --card-shadow: rgba(30, 20, 40, 0.35);
  }
  * { margin: 0; padding: 0; box-sizing: border-box; }
  html, body { width: 1200px; height: 750px; overflow: hidden; }
  body {
    background: var(--canvas-bg);
    font-family: "Roboto", Arial, sans-serif;
    position: relative;
  }
  .card {
    position: absolute;
    width: 540px;
    height: 309px;
    border-radius: 22px;
    overflow: hidden;
    background: radial-gradient(ellipse at 60% 20%, var(--card-light) 0%, var(--card-mid) 40%, var(--card-dark) 100%);
    box-shadow: 0 10px 28px var(--card-shadow);
  }
  .card--front { left: 45px; top: 220px; }
  .card--back { left: 615px; top: 220px; }

  .wordmark {
    position: absolute;
    font-family: "Roboto", Arial, sans-serif;
    font-weight: 400;
    color: var(--wordmark-grey);
    letter-spacing: -0.5px;
    line-height: 1;
    white-space: nowrap;
  }
  .card--front .wordmark { left: 48px; top: 112px; font-size: 44px; }
  .card--back .wordmark { left: 0; right: 0; top: 130px; text-align: center; font-size: 48px; }

  .swoosh { position: absolute; left: 0; top: 0; width: 540px; height: 309px; }

  .holder-name {
    position: absolute;
    right: 34px;
    top: 232px;
    font-family: "Cinzel", Georgia, serif;
    font-weight: 600;
    font-size: 19px;
    letter-spacing: 1px;
    color: #ffffff;
  }
  .contact {
    position: absolute;
    left: 48px;
    top: 196px;
    list-style: none;
    color: var(--contact-white);
    font-size: 13px;
  }
  .contact li {
    display: flex;
    align-items: center;
    gap: 8px;
    margin-bottom: 10px;
  }
  .contact svg { width: 12px; height: 12px; fill: var(--brand-blue); }
</style>
</head>
<body>
  <section class="card card--front" aria-label="Business card front">
    <span class="wordmark">Halvern Works</span>

    <ul class="contact">
      <li>
        <svg viewBox="0 0 12 12" aria-hidden="true"><path d="M3 1 L5 3.5 L4 5 Q5.2 7 7 8 L8.5 7 L11 9 L10 11 Q4 11 1 2 Z"/></svg>
        <span>614-387-2259</span>
      </li>
      <li>
        <svg viewBox="0 0 12 12" aria-hidden="true"><path d="M1 3 H11 V10 H1 Z M1.5 3.5 L6 7 L10.5 3.5" stroke="#2a2433" stroke-width="0.8"/></svg>
        <span>KateBrook@klbarrowvista.com</span>
      </li>
    </ul>

    <svg class="swoosh" viewBox="0 0 540 309" aria-hidden="true">
      <path d="M0 272 C150 262 260 255 360 228 C430 210 490 196 540 200" fill="none" stroke="var(--swoosh-silver)" stroke-width="3"/>
      <path d="M0 280 C160 272 270 262 370 236 C440 218 495 206 540 210 L540 309 L0 309 Z" fill="var(--brand-blue)"/>
      <path d="M0 290 C150 284 280 278 380 250 C450 230 500 222 540 224 L540 309 L0 309 Z" fill="var(--brand-blue-deep)" opacity="0.45"/>
    </svg>
    <span class="holder-name">KATE BROOK</span>
  </section>

  <section class="card card--back" aria-label="Business card back">
    <span class="wordmark">Halvern Works</span>
  </section>
</body>
</html>
```